Marbrook Cupcakes Website

We need a new website. We make Texas-size gourmet cupcakes and cupcake jars. We want a website similar to the one KEYlane is hosting and made. They're charging too much per month. I would like to have Blu Otter host it. see the current site at: marbrookcupcakes.com

```html
<!DOCTYPE html>
<html lang="en">
<head>
<meta charset="utf-8">
<title>Marbrook Cupcakes</title>
<link rel="stylesheet" href="https://fonts.googleapis.com/css2?family=Kaushan+Script&family=Open+Sans:wght@400;600;700&family=Titillium+Web:ital,wght@1,700&family=Bungee&display=swap">
<style>
:root{
  --teal:#77cfd4;
  --brown:#4a1e0f;
  --ink:#3d1a0c;
  --pink:#f06fa2;
  --wood-a:#7a3a1e;
  --wood-b:#a4552c;
  --text:#3b3b3b;
  --white:#ffffff;
}
*{margin:0;padding:0;box-sizing:border-box}
html,body{width:1200px;height:4286px;overflow:hidden;background:var(--white)}
body{position:relative;font-family:"Open Sans",sans-serif;color:var(--text)}
.abs{position:absolute}
.pill{position:absolute;background:var(--teal);color:var(--ink);font-weight:700;border-radius:30px;display:flex;align-items:center;justify-content:center;font-size:17px;letter-spacing:.3px}

/* nav */
.nav{position:absolute;left:0;top:0;width:1200px;height:85px;background:var(--white);z-index:3}
.nav a{position:absolute;top:32px;font-size:16px;color:var(--ink);text-decoration:none}
.nav .active{border-top:3px solid var(--ink);padding-top:4px;top:26px}
.brand{position:absolute;left:520px;top:-5px;width:160px;height:160px;border-radius:50%;background:var(--white);z-index:4;display:flex;align-items:center;justify-content:center;text-align:center;font-size:17px;font-weight:700;color:var(--teal);line-height:1.2}

/* hero */
.hero{position:absolute;left:0;top:85px;width:1200px;height:640px;background:linear-gradient(115deg,var(--wood-a),var(--wood-b) 55%,#6b3118)}
.hero h1{position:absolute;left:110px;top:185px;font-family:"Kaushan Script",cursive;font-weight:400;font-size:54px;line-height:62px;color:var(--white)}
.hero p{position:absolute;left:112px;top:327px;width:500px;font-size:17px;line-height:26px;color:var(--white)}

.section-title{position:absolute;left:0;width:1200px;text-align:center;font-family:"Kaushan Script",cursive;font-weight:400;font-size:48px;color:var(--ink)}
.section-title span{color:var(--teal)}
.rule{position:absolute;height:3px;background:var(--ink);border-radius:2px}

/* products */
.product{position:absolute;width:318px;height:355px;border-radius:20px;background:var(--teal);overflow:hidden}
.product .shot{height:266px;background:radial-gradient(circle at 50% 55%,#c98a5b,var(--wood-a) 75%)}
.product .tag{text-align:center;font-family:"Kaushan Script",cursive;font-size:14px;color:var(--white);margin-top:10px}
.product .name{text-align:center;font-family:"Titillium Web",sans-serif;font-style:italic;font-weight:700;font-size:26px;color:var(--white);line-height:34px}
.product.is-hot{background:var(--pink)}

/* about */
.about-copy{position:absolute;left:133px;top:1843px;width:495px;font-size:16px;line-height:28px;color:var(--text)}
.about-mark{position:absolute;left:133px;top:2025px;font-size:30px;font-weight:600;color:var(--teal)}
.portrait{position:absolute;left:655px;top:1748px;width:422px;height:422px;border-radius:50%;background:radial-gradient(circle at 50% 40%,#e6e6e6,#a9a9a9)}
.portrait-ring{position:absolute;left:653px;top:1732px;width:426px;height:426px;border-radius:50%;border:12px solid var(--teal);border-left-color:transparent;border-bottom-color:transparent;transform:rotate(-25deg)}

/* recipes */
.recipe{position:absolute;width:311px;height:430px}
.recipe .frame{position:absolute;left:0;top:0;width:311px;height:430px;background:var(--white);border-radius:16px}
.recipe .shot{position:absolute;left:0;top:0;width:311px;height:416px;border-radius:16px;background:radial-gradient(circle at 50% 65%,#c98a5b,var(--wood-a) 75%)}
.recipe .label{position:absolute;top:40px;left:0;width:100%;text-align:center;font-family:"Bungee",sans-serif;font-size:36px;color:var(--pink);-webkit-text-stroke:1.5px var(--white)}
.recipe.is-hot .frame{background:var(--pink)}

/* blog */
.blog-lead{position:absolute;left:120px;top:3166px;width:960px;text-align:center;font-size:16px;line-height:28px}
.post{position:absolute;width:305px;height:443px;background:var(--white);border-radius:18px;box-shadow:0 4px 18px rgba(0,0,0,.12);overflow:hidden}
.post .shot{height:225px;background:radial-gradient(circle at 40% 60%,#d9a27a,var(--wood-a) 75%)}
.post .date{position:absolute;right:8px;top:10px;width:34px;height:48px;border-radius:16px;background:var(--teal);color:var(--white);text-align:center;font-weight:700;font-size:15px;line-height:16px;padding-top:7px}
.post .date small{display:block;font-size:9px}
.post h3{margin:30px 30px 0;font-size:19px;line-height:26px;color:var(--ink);font-weight:700}
.post p{margin:16px 30px 0;font-size:13.5px;line-height:21px;color:#555}

/* footer */
.footer{position:absolute;left:0;top:3800px;width:1200px;height:486px;background:var(--brown)}
.newsletter-title{position:absolute;left:110px;top:3910px;font-family:"Kaushan Script",cursive;font-weight:400;font-size:46px;color:var(--white)}
.signup{position:absolute;left:111px;top:4025px;width:977px;height:66px;border:2px solid var(--white);display:flex}
.signup .field{flex:1;color:var(--white);font-size:17px;padding-left:28px;display:flex;align-items:center}
.signup .btn{width:222px;background:var(--teal);color:var(--ink);font-weight:700;font-size:20px;display:flex;align-items:center;justify-content:center}
.contact{position:absolute;top:4137px;color:var(--white);font-size:17px;line-height:26px;white-space:nowrap}
.contact .icon{width:44px;height:44px;border-radius:50%;background:var(--white);display:flex;align-items:center;justify-content:center;margin-bottom:18px}
.copyright{position:absolute;left:885px;top:4224px;color:var(--white);font-size:17px}
</style>
</head>
<body>

<nav class="nav">
  <a class="active" style="left:110px">Home</a>
  <a style="left:203px">Menus</a>
  <a style="left:300px">About Us</a>
  <a style="left:411px">Our Products</a>
  <a style="left:690px">Recipes</a>
  <a style="left:794px">Latest Cakes</a>
  <a style="left:934px">FAQ</a>
  <a style="left:1007px">Contact Us</a>
</nav>
<div class="brand">Marbrook<br>Cupcakes</div>

<section class="hero" role="img" aria-label="Two oversized cupcakes with coconut pecan frosting on glass stands over a wooden background">
  <h1>Indulge in Texas-<br>Sized Gourmet Bliss</h1>
  <p>Handcrafted daily, our oversized cupcakes and rich cupcake jars are the perfect treat for any occasion.</p>
</section>
<div class="pill" style="left:110px;top:489px;width:156px;height:40px">ORDER NOW</div>
<svg class="abs" style="left:0;top:580px" width="1200" height="150" viewBox="0 0 1200 150">
  <path d="M0 150 C200 40 500 10 760 20 C950 28 1100 60 1200 55 L1200 150 Z" fill="var(--brown)"/>
  <path d="M0 150 C220 60 500 40 760 50 C950 58 1100 90 1200 110 L1200 150 Z" fill="var(--teal)"/>
  <path d="M0 150 C250 100 520 85 780 95 C960 102 1100 125 1200 150 Z" fill="var(--white)"/>
</svg>

<h2 class="section-title" style="top:728px">Our <span>Products</span></h2>
<div class="rule" style="left:504px;top:806px;width:192px"></div>

<div class="product" style="left:110px;top:840px"><div class="shot" role="img" aria-label="Cookies and cream cupcake"></div><div class="tag">Marbrook Cupcakes</div><div class="name">COOKIES 'N' CREAM</div></div>
<div class="product" style="left:441px;top:840px"><div class="shot" role="img" aria-label="Black velvet cupcake with chocolate frosting"></div><div class="tag">Marbrook Cupcakes</div><div class="name">BLACK VELVET</div></div>
<div class="product" style="left:771px;top:840px"><div class="shot" role="img" aria-label="Carrot cake cupcake topped with a pecan"></div><div class="tag">Marbrook Cupcakes</div><div class="name">CARROT CAKE</div></div>
<div class="product" style="left:110px;top:1213px"><div class="shot" role="img" aria-label="Strawberry cupcake with a fresh strawberry"></div><div class="tag">Marbrook Cupcakes</div><div class="name">STAWBERRY</div></div>
<div class="product is-hot" style="left:441px;top:1213px"><div class="shot" role="img" aria-label="Red velvet cupcake with cream cheese frosting"></div><div class="tag">Marbrook Cupcakes</div><div class="name">RED VELVET</div></div>
<div class="product" style="left:771px;top:1213px"><div class="shot" role="img" aria-label="Peanut caramel cupcake with chopped nut topping"></div><div class="tag">Marbrook Cupcakes</div><div class="name">PEANUTTY</div></div>
<div class="pill" style="left:502px;top:1606px;width:195px;height:39px;font-size:16px">VIEW ALL MENUS</div>

<h2 class="section-title" style="top:1748px;left:133px;width:auto;text-align:left">About <span>Us</span></h2>
<div class="rule" style="left:133px;top:1826px;width:168px"></div>
<p class="about-copy">Sed ut perspiciatis unde omnis iste natus error sit voluptatem accusantium doloremque laudantium, totam rem aperiam, eaque ipsa quae ab illo inventore veritatis et quasi architecto beatae vitae dicta sunt explicabo. Nemo enim ipsam voluptatem quia voluptas sit aspernatur aut odit aut fugit.</p>
<div class="about-mark">Marbrook Cupcakes</div>
<div class="pill" style="left:131px;top:2110px;width:403px;height:40px;font-size:16px">LEARN MORE MARBROOK CUPCAKES</div>
<div class="portrait-ring"></div>
<div class="portrait" role="img" aria-label="Portrait of the bakery owner in a dark suit"></div>

<svg class="abs" style="left:0;top:2238px" width="1200" height="736" viewBox="0 0 1200 736">
  <path d="M0 83 L110 83 C300 -10 900 -10 1090 83 L1200 83 L1200 650 L1090 650 C900 745 300 745 110 650 L0 650 Z" fill="var(--teal)"/>
</svg>
<h2 class="section-title" style="top:2303px">Our Recipes</h2>
<div class="rule" style="left:518px;top:2380px;width:164px"></div>
<div class="recipe" style="left:93px;top:2423px"><div class="frame" style="top:12px"></div><div class="shot" role="img" aria-label="German chocolate cupcake on a glass stand"></div><div class="label">GERMON</div></div>
<div class="recipe is-hot" style="left:438px;top:2423px"><div class="frame" style="top:12px;left:10px"></div><div class="shot" role="img" aria-label="Peanut caramel cupcake with nut topping"></div><div class="label">PEANUTTY</div></div>
<div class="recipe" style="left:783px;top:2423px"><div class="frame" style="top:12px;left:10px"></div><div class="shot" role="img" aria-label="Lemon cupcake with a lemon slice"></div><div class="label">LEMON</div></div>
<svg class="abs" style="left:25px;top:2626px" width="42" height="20" viewBox="0 0 42 20"><path d="M40 10 H3 M11 2 L3 10 L11 18" fill="none" stroke="var(--ink)" stroke-width="2.5"/></svg>
<svg class="abs" style="left:1134px;top:2626px" width="42" height="20" viewBox="0 0 42 20"><path d="M2 10 H39 M31 2 L39 10 L31 18" fill="none" stroke="var(--ink)" stroke-width="2.5"/></svg>

<h2 class="section-title" style="top:3060px">Marbrook Cupcakes <span>Blogs</span></h2>
<div class="rule" style="left:480px;top:3132px;width:240px"></div>
<p class="blog-lead">Sed ut perspiciatis unde omnis iste natus error sit voluptatem accusantium doloremque laudantium, totam rem aperiam, eaque ipsa quae ab illo inventore veritatis et quasi architecto beatae vitae dicta sunt explicabo.</p>
<article class="post" style="left:118px;top:3251px"><div class="shot" role="img" aria-label="Cupcakes with chocolate shavings"></div><div class="date">01<small>FEB</small></div><h3>Nemo enim ipsam voluptatem quia voluptas</h3><p>Sed ut perspiciatis unde omnis iste natus error sit voluptatem accusantium doloremque laudantium, totam rem aperiam, eaque ipsa quae</p></article>
<article class="post" style="left:451px;top:3251px"><div class="shot" role="img" aria-label="Strawberry cupcakes on glass stands"></div><div class="date">01<small>FEB</small></div><h3>Nemo enim ipsam voluptatem quia voluptas</h3><p>Sed ut perspiciatis unde omnis iste natus error sit voluptatem accusantium doloremque laudantium, totam rem aperiam, eaque ipsa quae</p></article>
<article class="post" style="left:782px;top:3251px"><div class="shot" role="img" aria-label="Red velvet cupcakes with crumb topping"></div><div class="date">01<small>FEB</small></div><h3>Nemo enim ipsam voluptatem quia voluptas</h3><p>Sed ut perspiciatis unde omnis iste natus error sit voluptatem accusantium doloremque laudantium, totam rem aperiam, eaque ipsa quae</p></article>

<footer class="footer"></footer>
<svg class="abs" style="left:0;top:3740px" width="1200" height="130" viewBox="0 0 1200 130">
  <path d="M0 20 C300 70 800 60 1200 0 L1200 70 C800 120 300 110 0 70 Z" fill="var(--teal)"/>
  <path d="M0 70 C300 110 800 120 1200 70 L1200 130 L0 130 Z" fill="var(--brown)"/>
</svg>
<h2 class="newsletter-title">Sign Up For Newsletter</h2>
<div class="signup"><div class="field">Sign up for our emails</div><div class="btn">SIGN UP</div></div>

<div class="contact" style="left:111px">
  <div class="icon"><svg width="22" height="26" viewBox="0 0 22 26"><path d="M11 24 C4 15 2 12 2 9 A9 9 0 0 1 20 9 C20 12 18 15 11 24 Z" fill="none" stroke="var(--brown)" stroke-width="2"/><circle cx="11" cy="9" r="3" fill="none" stroke="var(--brown)" stroke-width="2"/></svg></div>
  Location<br>United States, Marbrook Cupcakes
</div>
<div class="contact" style="left:406px">
  <div class="icon"><svg width="22" height="22" viewBox="0 0 22 22"><path d="M4 2 L8 2 L10 7 L7 9 C8 12 10 14 13 15 L15 12 L20 14 L20 18 C20 19 19 20 18 20 C9 20 2 13 2 4 C2 3 3 2 4 2 Z" fill="none" stroke="var(--brown)" stroke-width="2"/></svg></div>
  Phone<br>+1 555 014 2290
</div>
<div class="contact" style="left:601px">
  <div class="icon"><svg width="24" height="18" viewBox="0 0 24 18"><rect x="2" y="2" width="20" height="14" rx="2" fill="none" stroke="var(--brown)" stroke-width="2"/><path d="M2 3 L12 10 L22 3" fill="none" stroke="var(--brown)" stroke-width="2"/></svg></div>
  Email<br>hello@marbrookcupcakes.com
</div>
<div class="copyright">© 2025 Marbrook Cupcakes.</div>

</body>
</html>
```